Letterhead & Greeting Card Design Project

I need a few files prepared for dynamic digital printing: letterhead and 2 postcards with an envelope for each. Enclosed are specific directions from the printer for each file and overall. I have also enclosed mockups of what I would like on those designs and some raw files to work with.

Industry/Entity Type

Digital

```html
<!DOCTYPE html>
<html lang="en">
<head>
<meta charset="utf-8">
<title>Letterhead</title>
<link rel="stylesheet" href="https://fonts.googleapis.com/css2?family=Titillium+Web:wght@400;600&display=swap">
<style>
  :root {
    --paper: #ffffff;
    --ink: #3f3f3f;
    --ink-soft: #7a7a7a;
    --brand-grey: #4a4a4a;
    --brand-blue: #2ea3dc;
    --dot-grey: #b3b3b3;
  }
  * { margin: 0; padding: 0; box-sizing: border-box; }
  html, body {
    width: 933px;
    height: 1200px;
    overflow: hidden;
    background: var(--paper);
  }
  .letterhead {
    position: relative;
    width: 933px;
    height: 1200px;
    font-family: "Titillium Web", sans-serif;
    color: var(--ink);
    font-size: 16.6px;
    line-height: 26.6px;
  }
  .brand {
    position: absolute;
    left: 450px;
    top: 52px;
    display: flex;
    align-items: center;
    gap: 16px;
  }
  .brand-mark { width: 58px; height: 58px; }
  .brand-name {
    font-weight: 600;
    font-size: 64px;
    line-height: 1;
    letter-spacing: -0.5px;
    color: var(--brand-grey);
  }
  .block { position: absolute; left: 112px; }
  .date { top: 155px; }
  .recipient { top: 208px; }
  .salutation { top: 356px; }
  .body-copy { top: 406px; width: 716px; }
  .body-copy p + p { margin-top: 26.6px; }
  .closing { top: 892px; }
  .signature { top: 942px; }
  .footer-mark {
    position: absolute;
    left: 95px;
    top: 1075px;
    width: 120px;
    height: 120px;
  }
  .footer-address {
    position: absolute;
    left: 270px;
    top: 1122px;
    font-size: 17px;
    color: var(--ink-soft);
    font-family: "Titillium Web", sans-serif;
  }
</style>
</head>
<body>
<div class="letterhead">
  <header class="brand">
    <svg class="brand-mark" viewBox="0 0 58 58" aria-hidden="true">
      <circle cx="29" cy="29" r="22" fill="var(--brand-blue)"/>
    </svg>
    <span class="brand-name">lumenrow</span>
  </header>

  <div class="block date">November 08, 2012</div>

  <address class="block recipient" style="font-style:normal">
    John Doe<br>
    Account Name<br>
    Address 1<br>
    Address 2
  </address>

  <div class="block salutation">Dear Customer:</div>

  <div class="block body-copy">
    <p>Lorem ipsum dolor sit amet, consectetur adipiscing elit. Donec elementum velit sit amet libero fringilla adipiscing. Aliquam sollicitudin, leo vitae molestie facilisis, tellus ligula varius velit, vitae tincidunt lacus purus vitae nulla. Nulla imperdiet, odio quis ultrices ornare, diam est dictum lacus, et vehicula est magna at metus. Integer mattis lorem quis tortor accumsan ultrices ac ut massa. Duis eget metus ut risus scelerisque ornare quis eget dui. Aliquam lobortis dolor vitae magna volutpat eu facilisis tellus molestie. Seda a purus quis nibh lacinia interdum ut at leo. Sed sem dui, mollis in pellentesque sed, placerat non erat. Cum sociis natoque penatibus et magnis dis parturient montes, nascetur ridiculus mus. In lacinia arcu non felis laoreet sed convallis lectus tincidunt. Duis quis mauris et enim egestas molestie vel id sem.</p>
    <p>Integer consequat velit quis elit hendrerit imperdiet. Donec felis velit, volutpat vel convallis nec, sollicitudin et nulla. Pellentesque sodales elementum aliquam. Donec convallis, turpis sit amet laoreet ultricies, enim est elementum magna, dictum lobortis eros tellus quis diam. Nunc suscipit augue non nisl volutpat volutpat. Ut egestas ultrices purus, eget varius nibh placerat in. Cras leo ante, congue id ultricies a, ornare eu est. Curabitur eleifend tincidunt mi eget tristique.</p>
  </div>

  <div class="block closing">Thanking you,</div>

  <div class="block signature">
    John Doe<br>
    Company<br>
    Phone<br>
    Email
  </div>

  <svg class="footer-mark" viewBox="0 0 120 120" aria-hidden="true">
    <circle cx="60" cy="60" r="44" fill="var(--dot-grey)" opacity="0.5"/>
  </svg>

  <div class="footer-address">Street • City • State/Providence • Zip/Postal Code</div>
</div>
</body>
</html>
```